Honey Company from Florida Needs Sweet and Buzz-worthy Site

Website Requests:
-Deluxe 5-Page Website with SSL-Secure Online Store (Shopify)
-High-end imagery to appeal to a discerning consumer
-Detailed verbiage with strong SEO and easy readability
-Design principles: simple, chic, luxe, earthy
Pages:
1. Home {Local, Raw American Honey from Florida}
2. The Hive
> About Us
>Meet the Beekeepers
3. Buy Honey
> Shopify retail store
4. The Buzz {News, Recipes & More}
> Blog
5. Contact Us {We're Buzzin' to Meet You}
> Store Hours
> Phone Number
> Address
> Quick Contact Form
Attachments: Web design notes, Logo, Color Codes, Inspiration Photos
Target Market(s)
High-end honey consumer in the U.S.
Industry/Entity Type
Upscale honey enthusiasts; direct to consumer sales.
Coding
Coded - Design and coding required
Number of Pages Required
5+ page
Requirements
Must have
- Upscale look and feel, easy usability for quick sales.

```html
<!DOCTYPE html>
<html lang="en">
<head>
<meta charset="utf-8">
<title>Amber Hollow Apiary – Page Designs</title>
<link rel="stylesheet" href="https://fonts.googleapis.com/css2?family=Playfair+Display:wght@400;700;900&display=swap">
<style>
:root{
  --board:#a5a5a5;
  --white:#ffffff;
  --ink:#1c1c1c;
  --text:#3a3a3a;
  --muted:#8a8a8a;
  --band:#f4f4f4;
  --honey:#efcc5a;
  --gold:#e3bd55;
  --line:#d8d8d8;
}
*{box-sizing:border-box;margin:0;padding:0}
html,body{width:1079px;height:1200px;overflow:hidden}
body{background:var(--board);position:relative;font-family:"Playfair Display",serif;color:var(--text)}
.board-title{position:absolute;color:var(--white);font-size:17px;font-weight:400;letter-spacing:.5px;white-space:nowrap;transform:translateX(-50%)}
.page{position:absolute;width:521px;background:var(--white);transform:scale(.5929);transform-origin:0 0;overflow:hidden}
.page *{position:absolute}
.page .flow,.page .flow *{position:static}
.site-header{left:0;top:0;width:521px;height:60px;background:var(--white)}
.brand{left:83px;top:8px;width:74px;height:74px;border-radius:50%;background:var(--white);border:2px solid var(--ink);z-index:3;display:flex;align-items:center;justify-content:center;text-align:center;font-size:11px;font-weight:700;line-height:1.15;color:var(--ink)}
.brand span{position:static}
.search{left:284px;top:12px;width:85px;height:11px;border:1px solid var(--ink);border-radius:6px;font-size:6px;line-height:9px;padding-left:6px;color:var(--muted)}
.search-btn{left:355px;top:12px;width:14px;height:11px;background:var(--ink);border-radius:0 6px 6px 0}
.icon-cart,.icon-user{top:11px;width:13px;height:13px}
.nav{top:38px;font-size:8px;color:var(--ink);white-space:nowrap}
.hero{left:0;top:60px;width:521px;height:180px;background:linear-gradient(180deg,#a9bfcc 0%,#b7c3a4 22%,#7d9650 45%,#c1913f 62%,#7f8a3c 100%)}
.hero-title{left:0;width:100%;top:130px;text-align:center;font-size:26px;font-weight:700;color:var(--white);letter-spacing:.5px}
.band-gray{left:0;top:240px;width:521px;background:var(--band)}
.section-title{font-size:16px;font-weight:700;color:var(--ink);white-space:nowrap}
.bee{border-radius:50%;background:radial-gradient(circle at 45% 50%,#f3d15a 0 40%,#2a2a2a 41% 55%,#f3d15a 56%)}
.para{font-size:6.4px;line-height:10.4px;color:var(--text)}
.hex{clip-path:polygon(50% 0,100% 25%,100% 75%,50% 100%,0 75%,0 25%)}
.keeper-name{font-size:11px;font-weight:700;color:var(--gold);white-space:nowrap}
.keeper-role{font-size:9px;color:var(--ink);white-space:nowrap}
.portrait{width:140px;height:140px;border-radius:50%;border:3px solid var(--ink);box-shadow:0 0 0 3px var(--white),0 0 0 4px var(--gold);z-index:2}
.site-footer{left:0;width:521px;height:290px;background:linear-gradient(180deg,var(--white) 0%,var(--white) 60%,#fbf3de 100%);z-index:1}
.foot-brand{left:26px;top:87px;width:76px;height:76px;border-radius:50%;background:var(--white);border:2px solid var(--ink);display:flex;align-items:center;justify-content:center;text-align:center;font-size:11px;font-weight:700;line-height:1.15;color:var(--ink)}
.foot-brand span{position:static}
.foot-head{font-size:8px;font-weight:700;color:var(--ink);white-space:nowrap}
.foot-small{font-size:5.2px;line-height:10px;color:var(--text);white-space:nowrap}
.foot-tiny{font-size:4px;line-height:6px;color:var(--muted)}
.dot-icon{width:11px;height:11px;border-radius:50%;background:var(--honey)}
.field{left:346px;width:123px;height:11px;border:1px solid var(--ink);border-radius:6px;font-size:5.5px;line-height:9px;padding-left:7px;color:var(--muted)}
.signup-btn{left:346px;top:170px;width:123px;height:14px;border-radius:7px;background:var(--honey);font-size:6.5px;font-weight:700;line-height:14px;text-align:center;color:var(--ink)}
.foot-nav{top:207px;font-size:7px;color:var(--ink);white-space:nowrap}
.copyright{left:0;width:100%;top:262px;text-align:center;font-size:4.8px;color:var(--ink)}
.foot-curve{left:0;top:225px;width:521px;height:30px}
.post{width:374px;height:174px;background:var(--white)}
.post-text{top:31px;width:190px}
.post-title{font-size:12px;font-weight:700;line-height:13.5px;color:var(--ink)}
.post-title u{text-decoration:underline;text-underline-offset:2px}
.post .para{margin-top:9px}
.share{margin-top:8px;display:flex;gap:7px;align-items:center;font-size:6px;color:var(--ink)}
.share i{display:inline-block;width:6px;height:6px;border-radius:50%;background:var(--ink)}
.share em{font-style:normal;margin-left:6px}
.tile{width:209px;height:282px;background:var(--white)}
.tile-photo{left:0;top:0;width:209px;height:140px}
.tile-body{left:16px;top:153px;width:180px}
</style>
</head>
<body>

<h1 class="board-title" style="left:173px;top:26px">ABOUT HIVE</h1>
<h1 class="board-title" style="left:524px;top:32px">THE BUZZ VESION 1</h1>
<h1 class="board-title" style="left:871px;top:37px">THE BUZZ VESION 2</h1>

<!-- ===== The Hive page ===== -->
<section class="page" style="left:27px;top:74px;height:1644px">
  <header class="site-header">
    <div class="search">search</div><div class="search-btn"></div>
    <svg class="icon-cart" style="left:374px" viewBox="0 0 13 13"><path d="M1 2h2l2 6h6l1-4H4" fill="none" stroke="#e0a820" stroke-width="1.2"/><circle cx="6" cy="11" r="1" fill="#e0a820"/><circle cx="10" cy="11" r="1" fill="#e0a820"/></svg>
    <svg class="icon-user" style="left:393px" viewBox="0 0 13 13"><circle cx="6.5" cy="6.5" r="5.5" fill="none" stroke="#e0a820" stroke-width="1.2"/><circle cx="6.5" cy="5" r="1.8" fill="#e0a820"/><path d="M3 10.5c1-2 6-2 7 0" fill="none" stroke="#e0a820"/></svg>
    <span class="nav" style="left:180px">Home</span>
    <span class="nav" style="left:220px">The Hive</span>
    <span class="nav" style="left:271px">Buy Honey</span>
    <span class="nav" style="left:328px">The Buzz</span>
    <span class="nav" style="left:380px">Contact</span>
    <span class="bee" role="img" aria-label="Small bee illustration" style="left:252px;top:28px;width:10px;height:9px"></span>
  </header>
  <div class="brand"><span>Amber<br>Hollow</span></div>
  <div class="hero" role="img" aria-label="Row of wooden beehives in a green hillside field"></div>
  <h2 class="hero-title">THE HIVE</h2>

  <div class="band-gray" style="height:370px"></div>
  <span class="bee" role="img" aria-label="Bee illustration with dotted flight path" style="left:322px;top:262px;width:36px;height:30px"></span>
  <span class="bee" role="img" aria-label="Small bee illustration" style="left:158px;top:297px;width:16px;height:13px"></span>
  <h2 class="section-title" style="left:192px;top:286px">The Buzz About Us</h2>
  <svg style="left:36px;top:348px;width:196px;height:214px" viewBox="0 0 196 214"><polygon points="98,1 195,55 195,159 98,213 1,159 1,55" fill="none" stroke="#e8cf86" stroke-width="1"/></svg>
  <div class="hex" role="img" aria-label="Close-up of honeybees on a honeycomb" style="left:47px;top:333px;width:178px;height:205px;background:linear-gradient(140deg,#d6a23c,#8a5a1e 55%,#e2b255)"></div>
  <div style="left:239px;top:352px;width:192px">
    <p class="para flow">Sed ut perspiciatis unde omnis iste natus error sit voluptem accusantium doloremque laudantium, totam rem aperiam, eaque ipsa quae ab illo inventore veritatis et quasi architecto beatae vitae dicta sunt explicabo. Nemo enim ipsam voluptate m quia voluptas sit aspernatur aut odit aut fugit, sed quia con sequuntur magni dolores eos qui ratione voluptatem sequi nesciunt. Neque porro quisquam est, qui dolorem ipsquia dolor sit amet, consectetur, adipisci velit, sed quia non numq uam eius modi tempora incidunt ut labore et dolore magam aliquam quaerat voluptatem. Ut enim ad minima veniamquis nostrum exercitationem ullam corporis suscipit laboriosam, nisi ut aliquid ex ea commodi consequatur.</p>
    <p class="para flow" style="margin-top:10px">Quis autem vel eum iure reprehenderit qui in ea voluptate velit esse quam nihil molestiae consequatur, vel illum qui dolorem eum fugiat quo voluptas nulla pariatur</p>
  </div>

  <span class="bee" role="img" aria-label="Bee illustration with dotted flight path" style="left:133px;top:622px;width:32px;height:28px"></span>
  <h2 class="section-title" style="left:185px;top:637px">Meet the Beekeepers</h2>

  <h3 class="keeper-name" style="left:63px;top:697px">Walter Pruitt Jr</h3>
  <p class="keeper-role" style="left:62px;top:716px">Owner/Beekeeper</p>
  <p class="para" style="left:63px;top:735px;width:192px">Sed ut perspiciatis unde omnis iste natus error sit volutem accusantium doloremque laudantium, totam rem aperiam, eaque ipsa quae ab illo inventore veritatis et quasi architecto beatae vitae dicta sunt explicabo. Nemo enim ipsam voluptate m quia voluptas sit aspernatur aut odit aut fugit, sed quia con sequuntur magni dolores eos qui ratione voluptatem sequi nesciunt. Neque porro quisquam est, qui dolorem ipsquia dolor sit amet, consectetur, adipisci velit, sed quia nonum uam eius modi tempora incidunt ut labore</p>
  <div class="portrait" role="img" aria-label="Portrait of the owner holding a honeycomb frame" style="left:281px;top:695px;background:linear-gradient(160deg,#7fb3d8,#e9e2cf 55%,#d6a640)"></div>

  <div class="portrait" role="img" aria-label="Beekeeper in a white suit holding a frame among green trees" style="left:66px;top:869px;background:linear-gradient(160deg,#4f7a34,#e6e6e0 55%,#3d5e2a)"></div>
  <h3 class="keeper-name" style="left:239px;top:871px">Nora Vance</h3>
  <p class="keeper-role" style="left:238px;top:890px">Beekeeper</p>
  <p class="para" style="left:239px;top:909px;width:192px">Sed ut perspiciatis unde omnis iste natus error sit volutem accusantium doloremque laudantium, totam rem aperiam, eaque ipsa quae ab illo inventore veritatis et quasi architecto beatae vitae dicta sunt explicabo. Nemo enim ipsam voluptate m quia voluptas sit aspernatur aut odit aut fugit, sed quia con sequuntur magni dolores eos qui ratione voluptatem sequi nesciunt. Neque porro quisquam est, qui dolorem ipsquia dolor sit amet, consectetur, adipisci velit, sed quia nonum uam eius modi tempora incidunt ut labore</p>

  <h3 class="keeper-name" style="left:63px;top:1048px">Eli Marsh</h3>
  <p class="keeper-role" style="left:62px;top:1067px">Beekeeper</p>
  <p class="para" style="left:63px;top:1086px;width:192px">Sed ut perspiciatis unde omnis iste natus error sit volutem accusantium doloremque laudantium, totam rem aperiam, eaque ipsa quae ab illo inventore veritatis et quasi architecto beatae vitae dicta sunt explicabo. Nemo enim ipsam voluptate m quia voluptas sit aspernatur aut odit aut fugit, sed quia con sequuntur magni dolores eos qui ratione voluptatem sequi nesciunt. Neque porro quisquam est, qui dolorem ipsquia dolor sit amet, consectetur, adipisci velit, sed quia nonum uam eius modi tempora incidunt ut labore</p>
  <div class="portrait" role="img" aria-label="Beekeeper in a veiled suit holding a honey frame outdoors" style="left:281px;top:1047px;background:linear-gradient(160deg,#8fa56a,#e8e4da 50%,#c99a3b)"></div>

  <div class="portrait" role="img" aria-label="Beekeeper inspecting hive frames" style="left:66px;top:1222px;background:linear-gradient(160deg,#9fb36a,#f0e6cf 50%,#b98a3a)"></div>
  <h3 class="keeper-name" style="left:239px;top:1226px">Dana Whitlock</h3>
  <p class="keeper-role" style="left:238px;top:1245px">Marketing Director</p>
  <p class="para" style="left:239px;top:1264px;width:192px">Sed ut perspiciatis unde omnis iste natus error sit volutem accusantium doloremque laudantium, totam rem aperiam, eaque ipsa quae ab illo inventore veritatis et quasi architecto beatae vitae dicta sunt explicabo. Nemo enim ipsam voluptate m quia voluptas sit aspernatur aut odit aut fugit, sed quia con sequuntur magni dolores eos qui ratione voluptatem sequi nesciunt. Neque porro quisquam est, qui dolorem ipsquia dolor sit amet, consectetur, adipisci velit, sed quia nonum uam eius modi tempora incidunt ut labore</p>

  <footer class="site-footer" style="top:1360px">
    <span class="bee" role="img" aria-label="Two bees illustration" style="left:362px;top:32px;width:40px;height:32px"></span>
    <div class="foot-brand"><span>Amber<br>Hollow</span></div>
    <h4 class="foot-head" style="left:120px;top:88px">Contact</h4>
    <svg class="dot-icon" style="left:124px;top:109px" viewBox="0 0 11 11"><path d="M3.5 3c.5 2 2 3.6 4 4.3l.8-1" fill="none" stroke="#1c1c1c" stroke-width="1.2"/></svg>
    <p class="foot-small" style="left:142px;top:106px;line-height:7px">Phone:<br>(555) 210-4417</p>
    <svg class="dot-icon" style="left:124px;top:139px" viewBox="0 0 11 11"><path d="M5.5 9L3.3 5.3a2.3 2.3 0 1 1 4.4 0z" fill="#1c1c1c"/></svg>
    <p class="foot-small" style="left:142px;top:136px;line-height:7.5px">Location:<br>1480 Orchard Lane,<br>Lakeview, FL 30000</p>
    <h4 class="foot-head" style="left:234px;top:88px">Hours of Operation</h4>
    <p class="foot-small" style="left:234px;top:102px">Monday 9 a.m. – 6 p.m.<br>Tuesday 9 a.m. – 6 p.m.<br>Wednesday 9 a.m. – 6 p.m.<br>Thursday 9 a.m. – 6 p.m.<br>Friday 9 a.m. – 6 p.m.<br>Saturday 9 a.m. – 4 p.m.<br>Sunday Closed</p>
    <h4 class="foot-head" style="left:346px;top:88px">Sign-up for Our Emails</h4>
    <p class="foot-tiny" style="left:346px;top:104px;width:125px">Join our list for seasonal harvest notes, new jars and recipes sent to you</p>
    <div class="field" style="top:125px">Name</div>
    <div class="field" style="top:145px">Email</div>
    <div class="signup-btn" style="top:166px">SIGN UP NOW</div>
    <span class="dot-icon" style="left:25px;top:190px"></span>
    <p class="foot-small" style="left:42px;top:190px">Facebook: facebook .com/amberhollowhoney/</p>
    <span class="dot-icon" style="left:25px;top:206px"></span>
    <p class="foot-small" style="left:42px;top:206px">Instagram: instagram .com/amberhollowapiary/</p>
    <span class="foot-nav" style="left:238px">Home</span>
    <span class="foot-nav" style="left:278px">The Hive</span>
    <span class="foot-nav" style="left:329px">Buy Honey</span>
    <span class="foot-nav" style="left:386px">The Buzz</span>
    <span class="foot-nav" style="left:438px">Contact</span>
    <svg class="foot-curve" viewBox="0 0 521 30"><path d="M0 20 C130 8 260 30 380 14 S500 10 521 16" fill="none" stroke="#e8cf86" stroke-width="1" stroke-dasharray="3 3"/></svg>
    <p class="copyright">© 2021 All Rights Reserved.Terms &amp; Conditions Privacy Policy</p>
  </footer>
</section>

<!-- ===== The Buzz, list layout ===== -->
<section class="page" style="left:369px;top:74px;height:1816px">
  <header class="site-header">
    <div class="search">search</div><div class="search-btn"></div>
    <svg class="icon-cart" style="left:374px" viewBox="0 0 13 13"><path d="M1 2h2l2 6h6l1-4H4" fill="none" stroke="#e0a820" stroke-width="1.2"/><circle cx="6" cy="11" r="1" fill="#e0a820"/><circle cx="10" cy="11" r="1" fill="#e0a820"/></svg>
    <svg class="icon-user" style="left:393px" viewBox="0 0 13 13"><circle cx="6.5" cy="6.5" r="5.5" fill="none" stroke="#e0a820" stroke-width="1.2"/><circle cx="6.5" cy="5" r="1.8" fill="#e0a820"/><path d="M3 10.5c1-2 6-2 7 0" fill="none" stroke="#e0a820"/></svg>
    <span class="nav" style="left:180px">Home</span>
    <span class="nav" style="left:220px">The Hive</span>
    <span class="nav" style="left:271px">Buy Honey</span>
    <span class="nav" style="left:328px">The Buzz</span>
    <span class="nav" style="left:380px">Contact</span>
    <span class="bee" role="img" aria-label="Small bee illustration" style="left:358px;top:28px;width:10px;height:9px"></span>
  </header>
  <div class="brand"><span>Amber<br>Hollow</span></div>
  <div class="hero" role="img" aria-label="Row of wooden beehives in a green hillside field"></div>
  <h2 class="hero-title">THE BUZZ</h2>

  <div class="band-gray" style="height:1322px"></div>
  <span class="bee" role="img" aria-label="Bee illustration with dotted flight path" style="left:377px;top:243px;width:36px;height:30px"></span>
  <span class="bee" role="img" aria-label="Small bee illustration" style="left:111px;top:292px;width:16px;height:13px"></span>
  <h2 class="section-title" style="left:136px;top:287px">Honey Recipes, Bee News &amp; More</h2>

  <article class="post" style="left:57px;top:341px">
    <div class="hex" role="img" aria-label="Beekeeper tending a long row of orange hives" style="left:0;top:0;width:150px;height:174px;background:linear-gradient(170deg,#a9c3d8,#c9793a 50%,#7f9a4d)"></div>
    <div class="post-text" style="left:170px">
      <h3 class="post-title flow"><u>In the News:</u> Walter talks bees, real and unfiltered</h3>
      <p class="para flow">Sed ut perspiciatis unde omnis iste natus error sit volutem accusantium doloremque laudantium, totam rem aperiam, eaque ipsa quae ab illo inventore veritatis et quasi architecto beatae vitae dicta sunt explicabo. Nemo enim ipsam voluptate m quia voluptas sit aspernatur aut odit aut fugit, sed quia con sequuntur magni dolores eos qui ratione volupt</p>
      <div class="share flow"><i></i><i></i></div>
    </div>
  </article>

  <article class="post" style="left:57px;top:535px">
    <div class="post-text" style="left:22px">
      <h3 class="post-title flow"><u>Recipe:</u> Sweet n’ Savory Sweet Potatoes with Honey</h3>
      <p class="para flow">Sed ut perspiciatis unde omnis iste natus error sit volutem accusantium doloremque laudantium, totam rem aperiam, eaque ipsa quae ab illo inventore veritatis et quasi architecto beatae vitae dicta sunt explicabo. Nemo enim ipsam voluptate m quia voluptas sit aspernatur aut odit aut fugit, sed quia con sequuntur magni dolores eos qui ratione volupt</p>
      <div class="share flow"><i></i><i></i></div>
    </div>
    <div class="hex" role="img" aria-label="Honey dipper drizzling honey over a golden stack" style="left:223px;top:0;width:150px;height:174px;background:linear-gradient(160deg,#c07a2e,#f0b548 55%,#8a4a18)"></div>
  </article>

  <article class="post" style="left:57px;top:730px">
    <div class="hex" role="img" aria-label="Sunset over a tree and rows of hives in a lavender field" style="left:0;top:0;width:150px;height:174px;background:linear-gradient(170deg,#6c6f7a,#e7a64a 45%,#8a6a3c)"></div>
    <div class="post-text" style="left:170px">
      <h3 class="post-title flow"><u>In the News:</u> Walter saves thousands of bees after a car accident along S.R. 46</h3>
      <p class="para flow">Sed ut perspiciatis unde omnis iste natus error sit volutem accusantium doloremque laudantium, totam rem aperiam, eaque ipsa quae ab illo inventore veritatis et quasi architecto beatae vitae dicta sunt explicabo. Nemo enim ipsam voluptate m quia voluptas sit aspernatur aut odit aut fugi</p>
      <div class="share flow"><i></i><i></i></div>
    </div>
  </article>

  <article class="post" style="left:57px;top:924px">
    <div class="post-text" style="left:22px">
      <h3 class="post-title flow"><u>Honey Recipe:</u> Sweet n’ Savory Sweet Potatoes with Honey</h3>
      <p class="para flow">Sed ut perspiciatis unde omnis iste natus error sit volutem accusantium doloremque laudantium, totam rem aperiam, eaque ipsa quae ab illo inventore veritatis et quasi architecto beatae vitae dicta sunt explicabo. Nemo enim ipsam voluptate m quia voluptas sit aspernatur aut odit aut fugit</p>
      <div class="share flow"><i></i><i></i><em>~Pecan Granola</em></div>
    </div>
    <div class="hex" role="img" aria-label="Honey drizzled into a mug of tea beside lemons" style="left:223px;top:0;width:150px;height:174px;background:linear-gradient(160deg,#f2ece4,#e08a3a 50%,#c9a46a)"></div>
  </article>

  <article class="post" style="left:57px;top:1118px">
    <div class="hex" role="img" aria-label="Beekeeper holding a full honeycomb frame" style="left:0;top:0;width:150px;height:174px;background:linear-gradient(150deg,#c47a2a,#8a5a22 50%,#e0a45c)"></div>
    <div class="post-text" style="left:170px">
      <h3 class="post-title flow"><u>In the News:</u> Walter warns of the real problem facing food supply</h3>
      <p class="para flow">Sed ut perspiciatis unde omnis iste natus error sit volutem accusantium doloremque laudantium, totam rem aperiam, eaque ipsa quae ab illo inventore veritatis et quasi architecto beatae vitae dicta sunt explicabo. Nemo enim ipsam voluptate m quia voluptas sit aspernatur aut odit aut.</p>
      <div class="share flow"><i></i><i></i></div>
    </div>
  </article>

  <article class="post" style="left:57px;top:1313px">
    <div class="post-text" style="left:22px">
      <h3 class="post-title flow">Sweet Summertime Honey Strawberry Lemonade Popsicles</h3>
      <p class="para flow">Sed ut perspiciatis unde omnis iste natus error sit volutem accusantium doloremque laudantium, totam rem aperiam, eaque ipsa quae ab illo inventore veritatis et quasi architecto beatae vitae dicta sunt explicabo. Nemo enim ipsam voluptate m quia voluptas sit aspernatur aut odit aut fugit</p>
      <div class="share flow"><i></i><i></i></div>
    </div>
    <div class="hex" role="img" aria-label="Woman pouring honey in a bright kitchen" style="left:223px;top:0;width:150px;height:174px;background:linear-gradient(160deg,#e9e7df,#cfc6b4 50%,#e7b54a)"></div>
  </article>

  <footer class="site-footer" style="top:1535px">
    <span class="bee" role="img" aria-label="Two bees illustration" style="left:360px;top:30px;width:40px;height:32px"></span>
    <div class="foot-brand"><span>Amber<br>Hollow</span></div>
    <h4 class="foot-head" style="left:120px;top:88px">Contact</h4>
    <svg class="dot-icon" style="left:124px;top:109px" viewBox="0 0 11 11"><path d="M3.5 3c.5 2 2 3.6 4 4.3l.8-1" fill="none" stroke="#1c1c1c" stroke-width="1.2"/></svg>
    <p class="foot-small" style="left:142px;top:106px;line-height:7px">Phone:<br>(555) 210-4417</p>
    <svg class="dot-icon" style="left:124px;top:139px" viewBox="0 0 11 11"><path d="M5.5 9L3.3 5.3a2.3 2.3 0 1 1 4.4 0z" fill="#1c1c1c"/></svg>
    <p class="foot-small" style="left:142px;top:136px;line-height:7.5px">Location:<br>1480 Orchard Lane,<br>Lakeview, FL 30000</p>
    <h4 class="foot-head" style="left:234px;top:88px">Hours of Operation</h4>
    <p class="foot-small" style="left:234px;top:102px">Monday 9 a.m. – 6 p.m.<br>Tuesday 9 a.m. – 6 p.m.<br>Wednesday 9 a.m. – 6 p.m.<br>Thursday 9 a.m. – 6 p.m.<br>Friday 9 a.m. – 6 p.m.<br>Saturday 9 a.m. – 4 p.m.<br>Sunday Closed</p>
    <h4 class="foot-head" style="left:346px;top:88px">Sign-up for Our Emails</h4>
    <p class="foot-tiny" style="left:346px;top:104px;width:125px">Join our list for seasonal harvest notes, new jars and recipes sent to you</p>
    <div class="field" style="top:125px">Name</div>
    <div class="field" style="top:145px">Email</div>
    <div class="signup-btn" style="top:166px">SIGN UP NOW</div>
    <span class="dot-icon" style="left:25px;top:190px"></span>
    <p class="foot-small" style="left:42px;top:190px">Facebook: facebook .com/amberhollowhoney/</p>
    <span class="dot-icon" style="left:25px;top:206px"></span>
    <p class="foot-small" style="left:42px;top:206px">Instagram: instagram .com/amberhollowapiary/</p>
    <span class="foot-nav" style="left:238px">Home</span>
    <span class="foot-nav" style="left:278px">The Hive</span>
    <span class="foot-nav" style="left:329px">Buy Honey</span>
    <span class="foot-nav" style="left:386px">The Buzz</span>
    <span class="foot-nav" style="left:438px">Contact</span>
    <svg class="foot-curve" viewBox="0 0 521 30"><path d="M0 20 C130 8 260 30 380 14 S500 10 521 16" fill="none" stroke="#e8cf86" stroke-width="1" stroke-dasharray="3 3"/></svg>
    <p class="copyright">© 2021 All Rights Reserved.Terms &amp; Conditions Privacy Policy</p>
  </footer>
</section>

<!-- ===== The Buzz, grid layout ===== -->
<section class="page" style="left:717px;top:76px;height:1560px">
  <header class="site-header">
    <div class="search">search</div><div class="search-btn"></div>
    <svg class="icon-cart" style="left:374px" viewBox="0 0 13 13"><path d="M1 2h2l2 6h6l1-4H4" fill="none" stroke="#e0a820" stroke-width="1.2"/><circle cx="6" cy="11" r="1" fill="#e0a820"/><circle cx="10" cy="11" r="1" fill="#e0a820"/></svg>
    <svg class="icon-user" style="left:393px" viewBox="0 0 13 13"><circle cx="6.5" cy="6.5" r="5.5" fill="none" stroke="#e0a820" stroke-width="1.2"/><circle cx="6.5" cy="5" r="1.8" fill="#e0a820"/><path d="M3 10.5c1-2 6-2 7 0" fill="none" stroke="#e0a820"/></svg>
    <span class="nav" style="left:180px">Home</span>
    <span class="nav" style="left:220px">The Hive</span>
    <span class="nav" style="left:271px">Buy Honey</span>
    <span class="nav" style="left:328px">The Buzz</span>
    <span class="nav" style="left:380px">Contact</span>
    <span class="bee" role="img" aria-label="Small bee illustration" style="left:358px;top:28px;width:10px;height:9px"></span>
  </header>
  <div class="brand"><span>Amber<br>Hollow</span></div>
  <div class="hero" role="img" aria-label="Row of wooden beehives in a green hillside field"></div>
  <h2 class="hero-title">THE BUZZ</h2>

  <div class="band-gray" style="height:1075px"></div>
  <span class="bee" role="img" aria-label="Bee illustration with dotted flight path" style="left:377px;top:243px;width:36px;height:30px"></span>
  <span class="bee" role="img" aria-label="Small bee illustration" style="left:111px;top:292px;width:16px;height:13px"></span>
  <h2 class="section-title" style="left:136px;top:287px">Honey Recipes, Bee News &amp; More</h2>

  <article class="tile" style="left:44px;top:331px">
    <div class="tile-photo" role="img" aria-label="Beekeeper tending a long row of orange hives" style="background:linear-gradient(170deg,#a9c3d8,#c9793a 50%,#7f9a4d)"></div>
    <div class="tile-body">
      <h3 class="post-title flow"><u>In the News:</u> Walter talks bees, real and unfiltered</h3>
      <p class="para flow" style="margin-top:9px">Sed ut perspiciatis unde omnis iste natus error sit volutem accusantium doloremque laudantium, totam rem aperiam, eaque ipsa quae ab illo inventore veritatis et quasi archcto beatae vitae dicta sunt explicabo.o enim ipsam lupt te m quia voluptas sit aspernatur aut od.</p>
      <div class="share flow"><i></i><i></i></div>
    </div>
  </article>
  <article class="tile" style="left:267px;top:331px">
    <div class="tile-photo" role="img" aria-label="Honey drizzled into a mug of tea beside lemons" style="background:linear-gradient(160deg,#f2ece4,#e08a3a 50%,#c9a46a)"></div>
    <div class="tile-body">
      <h3 class="post-title flow"><u>Recipe:</u> Sweet n’ Savory Sweet Potatoes with Honey</h3>
      <p class="para flow" style="margin-top:9px">Sed ut perspiciatis unde omnis iste natus error sit volutem accusantium doloremque laudantium, totam rem aperiam, eaque ipsa quae ab illo inventore veritatis et quasi archcto beatae vitae dicta sunt explicabo.o enim ipsam lupt te m quia voluptas sit aspernatur aut od.</p>
      <div class="share flow"><i></i><i></i></div>
    </div>
  </article>

  <article class="tile" style="left:44px;top:637px">
    <div class="tile-photo" role="img" aria-label="Sunset over a tree and rows of hives in a lavender field" style="background:linear-gradient(170deg,#6c6f7a,#e7a64a 45%,#8a6a3c)"></div>
    <div class="tile-body">
      <h3 class="post-title flow"><u>In the News:</u> Walter saves thousands of bees after a car accident along S.R. 46</h3>
      <p class="para flow" style="margin-top:9px">Sed ut perspiciatis unde omnis iste natus error sit volutem accusantium doloremque laudantium, totam rem aperiam, eaque ipsa quae ab illo inventore veritatis et quasi archcto beatae vitae dicta sunt explicabo.o enim ipsam.</p>
      <div class="share flow"><i></i><i></i></div>
    </div>
  </article>
  <article class="tile" style="left:267px;top:637px">
    <div class="tile-photo" role="img" aria-label="Honey dipper drizzling honey over a golden stack" style="background:linear-gradient(160deg,#c07a2e,#f0b548 55%,#8a4a18)"></div>
    <div class="tile-body">
      <h3 class="post-title flow"><u>Honey Recipe:</u> Sweet n’ Savory Sweet Potatoes with Honey</h3>
      <p class="para flow" style="margin-top:9px">Sed ut perspiciatis unde omnis iste natus error sit volutem accusantium doloremque laudantium, totam rem aperiam, eaque ipsa quae ab illo inventore veritatis et quasi archcto beatae vitae dicta sunt explicabo.</p>
      <div class="share flow"><i></i><i></i><em>~Pecan Granola</em></div>
    </div>
  </article>

  <article class="tile" style="left:44px;top:941px">
    <div class="tile-photo" role="img" aria-label="Beekeeper holding a full honeycomb frame" style="background:linear-gradient(150deg,#c47a2a,#8a5a22 50%,#e0a45c)"></div>
    <div class="tile-body">
      <h3 class="post-title flow"><u>In the News:</u> Walter warns of the real problem facing food supply</h3>
      <p class="para flow" style="margin-top:9px">Sed ut perspiciatis unde omnis iste natus error sit volutem accusantium doloremque laudantium, totam rem aperiam, eaque ipsa quae ab illo inventore veritatis et quasi archcto beatae vitae dicta sunt explicabo.</p>
      <div class="share flow"><i></i><i></i></div>
    </div>
  </article>
  <article class="tile" style="left:267px;top:941px">
    <div class="tile-photo" role="img" aria-label="Woman pouring honey in a bright kitchen" style="background:linear-gradient(160deg,#e9e7df,#cfc6b4 50%,#e7b54a)"></div>
    <div class="tile-body">
      <h3 class="post-title flow">Sweet Summertime Honey Strawberry Lemonade Popsicles</h3>
      <p class="para flow" style="margin-top:9px">Sed ut perspiciatis unde omnis iste natus error sit volutem accusantium doloremque laudantium, totam rem aperiam, eaque ipsa quae ab illo inventore veritatis et quasi archcto beatae vitae dicta sunt explicabo.</p>
      <div class="share flow"><i></i><i></i></div>
    </div>
  </article>

  <footer class="site-footer" style="top:1277px">
    <span class="bee" role="img" aria-label="Two bees illustration" style="left:372px;top:22px;width:40px;height:32px"></span>
    <div class="foot-brand"><span>Amber<br>Hollow</span></div>
    <h4 class="foot-head" style="left:120px;top:88px">Contact</h4>
    <svg class="dot-icon" style="left:124px;top:109px" viewBox="0 0 11 11"><path d="M3.5 3c.5 2 2 3.6 4 4.3l.8-1" fill="none" stroke="#1c1c1c" stroke-width="1.2"/></svg>
    <p class="foot-small" style="left:142px;top:106px;line-height:7px">Phone:<br>(555) 210-4417</p>
    <svg class="dot-icon" style="left:124px;top:139px" viewBox="0 0 11 11"><path d="M5.5 9L3.3 5.3a2.3 2.3 0 1 1 4.4 0z" fill="#1c1c1c"/></svg>
    <p class="foot-small" style="left:142px;top:136px;line-height:7.5px">Location:<br>1480 Orchard Lane,<br>Lakeview, FL 30000</p>
    <h4 class="foot-head" style="left:234px;top:88px">Hours of Operation</h4>
    <p class="foot-small" style="left:234px;top:102px">Monday 9 a.m. – 6 p.m.<br>Tuesday 9 a.m. – 6 p.m.<br>Wednesday 9 a.m. – 6 p.m.<br>Thursday 9 a.m. – 6 p.m.<br>Friday 9 a.m. – 6 p.m.<br>Saturday 9 a.m. – 4 p.m.<br>Sunday Closed</p>
    <h4 class="foot-head" style="left:346px;top:88px">Sign-up for Our Emails</h4>
    <p class="foot-tiny" style="left:346px;top:104px;width:125px">Join our list for seasonal harvest notes, new jars and recipes sent to you</p>
    <div class="field" style="top:125px">Name</div>
    <div class="field" style="top:145px">Email</div>
    <div class="signup-btn" style="top:166px">SIGN UP NOW</div>
    <span class="dot-icon" style="left:25px;top:190px"></span>
    <p class="foot-small" style="left:42px;top:190px">Facebook: facebook .com/amberhollowhoney/</p>
    <span class="dot-icon" style="left:25px;top:206px"></span>
    <p class="foot-small" style="left:42px;top:206px">Instagram: instagram .com/amberhollowapiary/</p>
    <span class="foot-nav" style="left:238px">Home</span>
    <span class="foot-nav" style="left:278px">The Hive</span>
    <span class="foot-nav" style="left:329px">Buy Honey</span>
    <span class="foot-nav" style="left:386px">The Buzz</span>
    <span class="foot-nav" style="left:438px">Contact</span>
    <svg class="foot-curve" viewBox="0 0 521 30"><path d="M0 20 C130 8 260 30 380 14 S500 10 521 16" fill="none" stroke="#e8cf86" stroke-width="1" stroke-dasharray="3 3"/></svg>
    <p class="copyright">© 2021 All Rights Reserved.Terms &amp; Conditions Privacy Policy</p>
  </footer>
</section>

</body>
</html>
```